RTavenor Business Cards & Letterhead

I have a logo but need a design for some new business cards. We are a Design-Build Firm that specializes in the design and construction of commercial projects.
the cards need to be professional. no cartoon stuff.
i would like to have the cards in AI format so I can update the card as needed. Logo is provided.
Our Address is: 4187 Marlowe Ct. Fenwick, Westbrook County 27614

```html
<!DOCTYPE html>
<html lang="en">
<head>
<meta charset="utf-8">
<title>RTavenor Business Card</title>
<link href="https://fonts.googleapis.com/css2?family=Roboto:wght@400;700;900&display=swap" rel="stylesheet">
<style>
  :root {
    --backdrop: #979797;
    --navy-deep: #04365b;
    --navy-mid: #0a5685;
    --navy-light: #0f6ca4;
    --card-white: #ffffff;
    --logo-grey: #545454;
    --accent-blue: #1677b7;
    --text-dark: #2a2a2a;
  }
  * { margin: 0; padding: 0; box-sizing: border-box; }
  html, body {
    width: 1200px;
    height: 1000px;
    overflow: hidden;
    background: var(--backdrop);
    font-family: "Roboto", Arial, sans-serif;
  }
  .canvas { position: relative; width: 1200px; height: 1000px; }

  .card {
    position: absolute;
    left: 293px;
    width: 615px;
    height: 351px;
  }
  .card--front {
    top: 110px;
    border-radius: 30px 30px 160px 24px;
    background: linear-gradient(60deg, var(--navy-deep) 0%, var(--navy-deep) 25%, var(--navy-mid) 55%, var(--navy-light) 100%);
  }
  .card--back {
    top: 519px;
    border-radius: 30px 30px 24px 160px;
    background: var(--card-white);
  }

  .wordmark {
    position: absolute;
    display: flex;
    align-items: center;
    font-weight: 900;
    line-height: 1;
    white-space: nowrap;
  }
  .wordmark__square {
    display: inline-block;
    margin-right: 10px;
  }
  .card--front .wordmark {
    left: 150px;
    top: 155px;
    font-size: 46px;
    letter-spacing: 3px;
    color: var(--card-white);
  }
  .card--front .wordmark__square {
    width: 34px; height: 34px;
    background: var(--card-white);
  }
  .card--back .wordmark {
    right: 33px;
    top: 48px;
    font-size: 44px;
    letter-spacing: 1.5px;
    color: var(--logo-grey);
  }
  .card--back .wordmark__square {
    width: 32px; height: 32px;
    background: var(--logo-grey);
  }

  .contact {
    position: absolute;
    right: 52px;
    top: 127px;
    text-align: right;
    font-size: 16px;
    line-height: 19px;
    color: var(--text-dark);
  }
  .contact__name {
    font-weight: 700;
    color: var(--accent-blue);
    letter-spacing: 0.2px;
  }
  .contact__group--reach { margin-top: 24px; }
  .contact__group--address { margin-top: 19px; }
</style>
</head>
<body>
<main class="canvas">
  <section class="card card--front" aria-label="Business card front">
    <div class="wordmark"><span class="wordmark__square"></span>RTAVENOR</div>
  </section>

  <section class="card card--back" aria-label="Business card back">
    <div class="wordmark"><span class="wordmark__square"></span>RTAVENOR</div>
    <div class="contact">
      <div class="contact__group">
        <p class="contact__name">RONALD TAVENOR</p>
        <p class="contact__role">Founder/President</p>
      </div>
      <div class="contact__group contact__group--reach">
        <p>ronald@rtavenor.com</p>
        <p>www.rtavenor.com</p>
        <p>555-014-8832</p>
      </div>
      <div class="contact__group contact__group--address">
        <p>4187 Marlowe Ct. Fenwick</p>
        <p>Westbrook County 27614</p>
      </div>
    </div>
  </section>
</main>
</body>
</html>
```